Business Card Design for Occupational Medicine Start Up Company

We need to design a professional business card. We are a healthcare company providing occupational medicine services to blue collar industries. We are professional, efficient and high quality service providers.

Target Market(s)

Blue Collar Industry: Shipbuilding, Ports, Trucking Companies; The Executives and Safety Officers for these companies

Industry/Entity Type

Healthcare

Contact Information for Business Card

Logo, Name, Title, Email, Phone

Other font styles liked:
• Please match our Brand Guide

Requirements
Must have
• Our Company Colors and Logo

```html
<!DOCTYPE html>
<html lang="en">
<head>
<meta charset="utf-8">
<title>CrewWell Business Card</title>
<link rel="stylesheet" href="https://fonts.googleapis.com/css2?family=Poppins:wght@400;500;600;700&display=swap">
<style>
  :root {
    --backdrop: #e9dccb;
    --paper: #fbfbfa;
    --navy: #1f2a7a;
    --sky: #1ba3dc;
    --gold: #f0a92a;
    --ink: #16172b;
    --shadow: rgba(80, 55, 30, 0.22);
  }
  * { box-sizing: border-box; margin: 0; padding: 0; }
  html, body {
    width: 1200px;
    height: 800px;
    overflow: hidden;
    background: var(--backdrop);
    font-family: "Poppins", sans-serif;
    color: var(--ink);
  }
  .canvas {
    position: relative;
    width: 1200px;
    height: 800px;
    display: flex;
    align-items: center;
    justify-content: center;
    gap: 40px;
  }
  .card {
    position: relative;
    width: 540px;
    height: 310px;
    background: var(--paper);
    box-shadow: 0 10px 28px var(--shadow);
    overflow: hidden;
  }

  /* stripe group */
  .stripes {
    position: absolute;
    top: 0;
    bottom: 0;
    display: flex;
    gap: 9px;
  }
  .stripes span { width: 5px; height: 100%; }
  .stripe-sky { background: var(--sky); }
  .stripe-navy { background: var(--navy); }
  .stripe-gold { background: var(--gold); }

  /* front */
  .card-front .stripes-left { left: 22px; }
  .card-front .stripes-right { right: 22px; }
  .brand {
    position: absolute;
    inset: 0;
    display: flex;
    align-items: center;
    justify-content: center;
    gap: 12px;
  }
  .brand-dot {
    width: 22px;
    height: 22px;
    border-radius: 50%;
    background: var(--navy);
  }
  .brand-name {
    font-weight: 600;
    font-size: 34px;
    letter-spacing: 2px;
    color: var(--navy);
    text-transform: uppercase;
  }

  /* back */
  .card-back .stripes-right { left: 418px; }
  .contact-rail {
    position: absolute;
    left: 44px;
    top: 0;
    width: 2px;
    height: 250px;
    background: var(--navy);
  }
  .rail-icon {
    position: absolute;
    left: 32px;
    width: 26px;
    height: 26px;
    display: flex;
    align-items: center;
    justify-content: center;
  }
  .rail-icon::before {
    content: "";
    position: absolute;
    inset: 2px;
    background: var(--navy);
    border-radius: 4px;
    transform: rotate(45deg);
  }
  .rail-icon svg { position: relative; width: 12px; height: 12px; fill: #fff; }
  .icon-person { top: 82px; }
  .icon-phone { top: 152px; }
  .icon-mail { top: 194px; }
  .icon-pin { top: 236px; }

  .holder-name {
    position: absolute;
    left: 80px;
    top: 56px;
    font-size: 24px;
    font-weight: 400;
    line-height: 1;
  }
  .holder-name strong { font-weight: 700; }
  .holder-title {
    position: absolute;
    left: 82px;
    top: 86px;
    font-size: 12px;
    font-weight: 500;
  }
  .contact-line {
    position: absolute;
    left: 82px;
    font-size: 12px;
    line-height: 15px;
  }
  .line-phone { top: 145px; }
  .line-mail { top: 188px; }
  .line-address { top: 231px; }

  .card-back .brand {
    inset: auto;
    left: 250px;
    top: 72px;
    width: 150px;
    height: 40px;
    gap: 8px;
  }
  .card-back .brand-dot { width: 14px; height: 14px; }
  .card-back .brand-name { font-size: 20px; letter-spacing: 1px; }
</style>
</head>
<body>
<main class="canvas">

  <article class="card card-back" aria-label="Business card, contact side">
    <div class="contact-rail"></div>

    <div class="rail-icon icon-person">
      <svg viewBox="0 0 12 12"><circle cx="6" cy="3.5" r="2.5"/><path d="M1 11c0-3 2.2-4.5 5-4.5s5 1.5 5 4.5z"/></svg>
    </div>
    <div class="rail-icon icon-phone">
      <svg viewBox="0 0 12 12"><path d="M2.5 1l2 2.2-1 1.3a6 6 0 0 0 4 4l1.3-1 2.2 2-1.2 1.5C5 11 1 7 1 2.2z"/></svg>
    </div>
    <div class="rail-icon icon-mail">
      <svg viewBox="0 0 12 12"><path d="M1 3h10v6.5H1z M1.5 3.3L6 6.8l4.5-3.5" stroke="#1f2a7a" stroke-width="0.8"/></svg>
    </div>
    <div class="rail-icon icon-pin">
      <svg viewBox="0 0 12 12"><path d="M6 1a3.6 3.6 0 0 1 3.6 3.6C9.6 7.4 6 11 6 11S2.4 7.4 2.4 4.6A3.6 3.6 0 0 1 6 1z"/><circle cx="6" cy="4.6" r="1.3" fill="#1f2a7a"/></svg>
    </div>

    <h1 class="holder-name"><strong>Dana</strong> Okoro</h1>
    <p class="holder-title">CEO &amp; Founder</p>

    <p class="contact-line line-phone">000 111 222 333<br>000 111 222 333</p>
    <p class="contact-line line-mail">yourgmail@name.com<br>www.websitename.com</p>
    <p class="contact-line line-address">Your Street Adrees Here<br>New Yerk, sity - 000</p>

    <div class="brand">
      <span class="brand-dot"></span>
      <span class="brand-name">CrewWell</span>
    </div>

    <div class="stripes stripes-right">
      <span class="stripe-sky"></span><span class="stripe-navy"></span><span class="stripe-gold"></span>
    </div>
  </article>

  <article class="card card-front" aria-label="Business card, brand side">
    <div class="stripes stripes-left">
      <span class="stripe-sky"></span><span class="stripe-navy"></span><span class="stripe-gold"></span>
    </div>
    <div class="brand">
      <span class="brand-dot"></span>
      <span class="brand-name">CrewWell</span>
    </div>
    <div class="stripes stripes-right">
      <span class="stripe-sky"></span><span class="stripe-navy"></span><span class="stripe-gold"></span>
    </div>
  </article>

</main>
</body>
</html>
```